Boutique custom software development company needs new business card

Our nearly 20 year old custom software development company would like to better include the fact that we are now providing Bitcoin services. These new services are B2B include education (how to acquire and securely hold Bitcoin) and integrating Bitcoin payments into existing ecommerce sites or other existing systems. Please keep the card clean and simple. Attached is our current design and some other files. vextorial.com

Target Market(s)

businesses owners interested in long term relationship

Industry/Entity Type

Custom software development and Bitcoin

Contact Information for Business Card

Dale Parker, dale@vextorial.com, vextorial.com, (888) 555-VXTRL

Font styles to use
Other font styles liked:
• monospace

Requirements
Must have
• double-sided
Nice to have
• clean and simple
Should not have
• physical address

```html
<!DOCTYPE html>
<html lang="en">
<head>
<meta charset="UTF-8">
<title>Vextorial — Business Card</title>
<link rel="stylesheet" href="https://fonts.googleapis.com/css2?family=Montserrat:wght@400;500;700;800&family=Lato:wght@400&display=swap">
<style>
  :root {
    --brand-blue: #3e72b8;
    --brand-orange: #ef7d22;
    --ink: #2b2b2b;
    --paper: #ffffff;
    --backdrop: #d9d4cc;
  }
  * { margin: 0; padding: 0; box-sizing: border-box; }
  html, body { width: 900px; height: 1200px; overflow: hidden; }
  body {
    background: var(--backdrop);
    position: relative;
    font-family: 'Montserrat', sans-serif;
  }
  .card {
    position: absolute;
    left: 80px;
    width: 742px;
    height: 440px;
    border-radius: 30px;
    overflow: hidden;
    box-shadow: 0 6px 14px rgba(0,0,0,0.25);
  }
  .card--front { top: 132px; background: var(--paper); }
  .card--back { top: 638px; background: var(--brand-blue); }

  /* Wordmark */
  .wordmark {
    position: absolute;
    display: flex;
    align-items: center;
    font-family: 'Montserrat', sans-serif;
    font-weight: 800;
    line-height: 1;
    white-space: nowrap;
  }
  .wordmark__square { background: var(--brand-orange); flex: none; }
  .wordmark__name { color: var(--brand-blue); }

  .card--front .wordmark { left: 68px; top: 203px; gap: 7px; }
  .card--front .wordmark__square { width: 34px; height: 34px; }
  .card--front .wordmark__name { font-size: 32px; letter-spacing: 0.3px; }
  .card--front .tagline {
    position: absolute;
    left: 68px; width: 245px; top: 254px;
    text-align: center;
    font-family: 'Lato', sans-serif;
    font-size: 15px;
    color: var(--brand-blue);
    white-space: nowrap;
  }

  .divider {
    position: absolute;
    left: 360px; top: 143px;
    width: 2px; height: 175px;
    background: var(--brand-blue);
  }

  .contact { position: absolute; left: 413px; top: 152px; }
  .contact__name {
    font-size: 28px; font-weight: 700;
    color: var(--brand-blue); line-height: 1.1;
  }
  .contact__role { font-size: 15px; color: var(--ink); margin-top: 2px; }
  .contact__list { list-style: none; margin-top: 27px; }
  .contact__item {
    display: flex; align-items: center; gap: 9px;
    font-size: 16px; color: var(--ink);
    height: 22.5px;
    white-space: nowrap;
  }
  .contact__icon { width: 14px; height: 14px; fill: var(--brand-blue); flex: none; }

  .bands { position: absolute; left: 0; top: 363px; width: 742px; height: 14px; }

  .card--back .wordmark { left: 68px; top: 139px; gap: 12px; }
  .card--back .wordmark__square { width: 100px; height: 100px; }
  .card--back .wordmark__name { color: var(--paper); font-size: 74px; letter-spacing: 0.5px; }
  .card--back .tagline {
    position: absolute;
    left: 0; width: 706px; top: 262px;
    text-align: center;
    font-family: 'Lato', sans-serif;
    font-size: 35px;
    letter-spacing: -0.5px;
    color: var(--paper);
    white-space: nowrap;
  }
</style>
</head>
<body>

  <section class="card card--front" aria-label="Card front">
    <div class="wordmark">
      <span class="wordmark__square"></span>
      <span class="wordmark__name">VEXTORIAL</span>
    </div>
    <p class="tagline">custom software &amp; bitcoin services</p>

    <div class="divider"></div>

    <div class="contact">
      <h1 class="contact__name">Dale Parker</h1>
      <p class="contact__role">Owner</p>
      <ul class="contact__list">
        <li class="contact__item">
          <svg class="contact__icon" viewBox="0 0 16 16" aria-hidden="true"><path d="M1 6c0-2 3-3.5 7-3.5S15 4 15 6v1.5h-3.5V6c-1-.6-2.2-.8-3.5-.8S5.5 5.4 4.5 6v1.5H1z"/><path d="M3.5 9 5 7h6l1.5 2v5h-9z"/></svg>
          <span>(888) 555-VXTRL</span>
        </li>
        <li class="contact__item">
          <svg class="contact__icon" viewBox="0 0 16 16" aria-hidden="true"><path d="M1 3.5h14L8 9z"/><path d="M1 5l7 5.4L15 5v7.5H1z"/></svg>
          <span>dale@vextorial.com</span>
        </li>
        <li class="contact__item">
          <svg class="contact__icon" viewBox="0 0 16 16" aria-hidden="true"><circle cx="8" cy="8" r="7"/><path d="M5 4c1.5 0 2.5 1 2 2.5S4.5 8 4 9.5 3 10 2.5 9M10 11c.5-1.5 2-1.5 2.5-3" stroke="#fff" stroke-width="1.4" fill="none"/></svg>
          <span>www.vextorial.com</span>
        </li>
      </ul>
    </div>

    <svg class="bands" viewBox="0 0 742 14" aria-hidden="true">
      <polygon points="0,0 373,0 363,14 0,14" fill="var(--brand-orange)"/>
      <polygon points="388,0 742,0 742,14 378,14" fill="var(--brand-blue)"/>
    </svg>
  </section>

  <section class="card card--back" aria-label="Card back">
    <div class="wordmark">
      <span class="wordmark__square"></span>
      <span class="wordmark__name">VEXTORIAL</span>
    </div>
    <p class="tagline">custom software &amp; bitcoin services</p>
  </section>

</body>
</html>
```